Exclusive beauty salon needs a price list or services booklet

I need a new very attractive flyer for my beauty salon, containing information on the different services and their prices.
In attachment you can find a pdf of the "old" one, but I'd love to have a beautifully designed new one!
I'd love to have a booklet in format 148 x 148 mm, or in US format, containing 12 or 16 pages, but if you can offer other nice looking designs they are welcome!
The services that need to come in the booklet with their prices can all be found on my website: www.atelierverano.be, starting with
Gelaatsverzorging
Wimperverlenging
Suikerontharing
Wimperlifting
Permanente Make Up
Airbrush Tanning

Target Market(s)

woman from 20 to 89 years old

Industry/Entity Type

Beauty Salon

Font styles to use
Sans Serif

Colors

Designer to choose colors to be used in the design.

Requirements
Must have
• a classy nice look, it must contain details about the services from my beauty salon and their prices, and nice pictures.
• The Names, prices and explanations of the services can easily be found on my website: www.atelierverano.be
Nice to have
• In attachment you can find the "old" price list in pdf, what I need now is a "new booklet" with the new logo and updated services price list.
• I need a very nice and attractive looking booklet, classy chique, Paris chique, looking very expensive.
Should not have
• Not too much colors, not too curly, but still feminine

```html
<!DOCTYPE html>
<html lang="nl">
<head>
<meta charset="utf-8">
<title>Atelier Verano – Gelaatsverzorging</title>
<link rel="stylesheet" href="https://fonts.googleapis.com/css2?family=Source+Sans+3:ital,wght@0,400;1,400&display=swap">
<style>
  :root {
    --backdrop: #b0d1d2;
    --paper: #f7f6f3;
    --paper-shade: #ecebe7;
    --accent: #3fa7ae;
    --body-text: #8a8a8a;
    --sun-light: #f2b41c;
    --sun-deep: #c98a06;
    --skin-light: #f6e6e3;
    --skin-deep: #e9cfc9;
  }
  * { margin: 0; padding: 0; box-sizing: border-box; }
  html, body { width: 1200px; height: 700px; overflow: hidden; }
  body {
    background: var(--backdrop);
    font-family: "Source Sans 3", sans-serif;
    display: flex; align-items: center; justify-content: center;
  }
  .spread {
    display: flex;
    width: 1100px; height: 370px;
    box-shadow: 0 6px 18px rgba(0,0,0,0.12);
  }
  .page { width: 550px; height: 370px; display: flex; }
  .page--left .text-column { background: linear-gradient(to right, var(--paper), var(--paper-shade)); }
  .page--right .text-column { background: linear-gradient(to left, var(--paper), var(--paper-shade)); }
  .photo { width: 240px; height: 100%; }
  .photo--sun { background: linear-gradient(160deg, var(--sun-light), var(--sun-deep)); }
  .photo--skin { width: 250px; background: linear-gradient(200deg, var(--skin-light), var(--skin-deep)); }
  .text-column {
    flex: 1;
    display: flex; flex-direction: column;
    padding: 24px 28px;
    text-align: center;
  }
  .page--left .text-column { justify-content: space-around; }
  .page--right .text-column { justify-content: space-between; padding-top: 16px; padding-bottom: 12px; }
  .service h2 {
    font-weight: 400; font-size: 13.5px;
    color: var(--accent);
    margin-bottom: 6px;
  }
  .service p {
    font-style: italic; font-size: 8.6px; line-height: 1.3;
    color: var(--body-text);
  }
  .service .price {
    font-style: italic; font-size: 11px;
    color: var(--accent);
    margin-top: 6px;
  }
  .inline-price { color: var(--accent); }
</style>
</head>
<body>
  <main class="spread">
    <section class="page page--left">
      <div class="photo photo--sun" role="img" aria-label="Foto van een model in een gele jurk tegen een gele achtergrond"></div>
      <div class="text-column">
        <article class="service">
          <h2>Cosmetische Verzorging</h2>
          <p>Verzorging i.o.v. Dermatoloog.<br>De verzorging bestaat uit: oppervlakkige reiniging,<br>verwijderen zwarte puntjes en onzuiverheden,<br>zuiverend masker.</p>
          <p class="price">€30</p>
        </article>
        <article class="service">
          <h2>Verwijderen van gerstekorrels</h2>
          <p>De prijs is afhankelijk van de hoeveelheid.<br>Vanaf <span class="inline-price">€15</span>, afhankelijk van de hoeveelheid</p>
        </article>
        <article class="service">
          <h2>Flash Nettoyant</h2>
          <p>Voor een gehydrateerde en comfortabele huid. Voor alle huidtypes, bij een vermoeide huid met weinig uitstraling. De verzorging bestaat uit: epilatie wenkbrauwen, oppervlakkige reiniging, diepe reiniging, crememasker aangepast aan huidconditie, serum, dagcème, handmassage.</p>
          <p class="price">€59 - 50 min.</p>
        </article>
      </div>
    </section>
    <section class="page page--right">
      <div class="text-column">
        <article class="service">
          <h2>Hydratation Essentielle</h2>
          <p>Voor een gehydrateerde, volle en frisse huid.<br>Geschikt voor alle huidtypes. De verzorging bestaat uit: epilatie wenkbrauwen, oppervlakkige reiniging, diepe reiniging, verwijderen van comedonen, massage van gelaat en décolleté, instituutmasker aangepast aan huidconditie, serum, dagcème, handmassage.</p>
          <p class="price">€65 - 60 min.</p>
        </article>
        <article class="service">
          <h2>Pureté Essentielle</h2>
          <p>Voor een gezonde en gezuiverde matte huid.<br>Voor gemengde tot vette huidtypes, met of zonder onzuiverheden. De verzorging bestaat uit: epilatie wenkbrauwen, oppervlakkige reiniging, diepe reiniging, verwijderen van comedonen, massage van gelaat en décolleté, instituutmasker aangepast aan huidconditie, serum, dagcème, handmassage.</p>
          <p class="price">€65 - 60 min.</p>
        </article>
        <article class="service">
          <h2>Luxe Verzorging Suprême Expérience</h2>
          <p>Luxe gelaatsverzorging LUMÈRE voor een herstelde, stralende huid met gladde trekken. De verzorging bestaat uit: epilatie wenkbrauwen, oppervlakkige reiniging, diepe reiniging, verwijderen van comedonen, voorbereidend masker, massage van gelaat en décolleté, instituutmasker aangepast aan huidconditie met extra anti aging actieve werkstoffen, serum, dagcème, handmassage.</p>
          <p class="price">€85 - 80 min.</p>
        </article>
      </div>
      <div class="photo photo--skin" role="img" aria-label="Portretfoto van een glimlachend model met een stralende huid tegen een lichtroze achtergrond"></div>
    </section>
  </main>
</body>
</html>
```